RVT Business Card Design

We are an independent auto dealer who specializes in commercial & fleet vehicles, we are family owned and operated and have been in business since 2001. We stock late model, low mileage, white trucks & vans. We mostly deal with companies in the construction and service industries. We are just looking to try to freshen up our old business card, we do not want to change the logo at this point, because it is well know within the southwest region & construction community. I have attached our logo and a PDF of our current business card for reference.
Updates
If the address is stacked there is no comma (,) after NE. Everyone keeps putting it in with this format and it is not correct.
482 Morrow Ave NE
Mesa Ridge, NM 87190
If the address is all on one line, then there will be a comma (,) after NE
482 Morrow Ave NE, Mesa Ridge, NM 87190
Please make changes accordingly, thank you for your attention in this matter.
Industry/Entity Type
Construction
Contact Information for Business Card
482 Morrow Ave NE, Mesa Ridge, NM 87190, Dorian Pellew, Vice President, dorian@rvtfleetcars.example, www.RVTfleetcars.example, ph 505-218-4470, fax 505-627-1904, cell 505-763-2085
Look and feel

```html
<!DOCTYPE html>
<html lang="en">
<head>
<meta charset="utf-8">
<title>RVT Business Card</title>
<link href="https://fonts.googleapis.com/css2?family=Cinzel:wght@400;700&display=swap" rel="stylesheet">
<style>
  :root {
    --backdrop: #e9e6e1;
    --card: #fbfbfb;
    --ink: #1c1c1c;
    --muted: #555555;
    --brand-red: #c8102e;
    --band-dark: #151515;
    --rule: #2a2a2a;
    --band-text: #ffffff;
  }
  html, body {
    margin: 0;
    width: 1200px;
    height: 600px;
    overflow: hidden;
    background: var(--backdrop);
    font-family: "Cinzel", serif;
  }
  .card {
    position: absolute;
    left: 180px;
    top: 60px;
    width: 840px;
    height: 480px;
    background: linear-gradient(135deg, #ffffff 0%, var(--card) 60%, #f1f1f1 100%);
    box-shadow: 0 10px 30px rgba(0,0,0,0.18);
    overflow: hidden;
  }
  .brand {
    position: absolute;
    left: 64px;
    top: 150px;
    margin: 0;
    font-size: 40px;
    line-height: 1;
    font-weight: 700;
    color: var(--ink);
    letter-spacing: 1px;
    white-space: nowrap;
  }
  .brand-mark {
    display: inline-block;
    width: 14px;
    height: 14px;
    background: var(--brand-red);
    margin-left: 12px;
    vertical-align: middle;
  }
  .divider-left {
    position: absolute;
    left: 64px;
    top: 232px;
    width: 400px;
    height: 1px;
    background: var(--rule);
  }
  .contact-list {
    position: absolute;
    left: 64px;
    top: 252px;
    margin: 0;
    padding: 0;
    list-style: none;
  }
  .contact-list li {
    display: flex;
    align-items: center;
    height: 30px;
    font-size: 16px;
    color: var(--ink);
    letter-spacing: 0.5px;
    white-space: nowrap;
  }
  .contact-list svg {
    width: 18px;
    height: 18px;
    margin-right: 12px;
    flex: none;
  }
  .person {
    position: absolute;
    right: 60px;
    top: 70px;
    text-align: right;
  }
  .person-name {
    margin: 0;
    font-size: 30px;
    font-weight: 700;
    color: var(--brand-red);
    font-variant: small-caps;
    letter-spacing: 1px;
    white-space: nowrap;
  }
  .person-title {
    margin: 4px 0 0;
    font-size: 16px;
    color: var(--muted);
    font-variant: small-caps;
    letter-spacing: 1px;
  }
  .divider-right {
    width: 150px;
    height: 1px;
    background: var(--rule);
    margin: 14px 0 14px auto;
  }
  .address {
    font-style: normal;
    font-size: 16px;
    line-height: 1.6;
    color: var(--ink);
    font-variant: small-caps;
    white-space: nowrap;
  }
  .edge-band {
    position: absolute;
    left: 0;
    bottom: 0;
    width: 100%;
    height: 40px;
    display: flex;
  }
  .edge-band-dark {
    flex: 0 0 520px;
    background: var(--band-dark);
  }
  .edge-band-red {
    flex: 1;
    background: var(--brand-red);
    display: flex;
    align-items: center;
    justify-content: flex-end;
    padding-right: 60px;
    color: var(--band-text);
    font-size: 14px;
    letter-spacing: 1px;
    white-space: nowrap;
  }
</style>
</head>
<body>
  <div class="card">
    <h1 class="brand">RVT Auto Sales<span class="brand-mark"></span></h1>
    <div class="divider-left"></div>
    <ul class="contact-list">
      <li>
        <svg viewBox="0 0 18 18" aria-hidden="true"><rect width="18" height="18" fill="var(--brand-red)"/><rect x="6" y="3" width="6" height="12" rx="1" fill="none" stroke="#fff" stroke-width="1.4"/></svg>
        505-763-2085
      </li>
      <li>
        <svg viewBox="0 0 18 18" aria-hidden="true"><rect width="18" height="18" fill="var(--brand-red)"/><path d="M5 4 L7.5 4 L8.5 7 L7 8 Q8.5 10.5 10 11 L11 9.5 L14 10.5 L14 13 Q8 14 5 4 Z" fill="#fff"/></svg>
        505-218-4470
      </li>
      <li>
        <svg viewBox="0 0 18 18" aria-hidden="true"><rect width="18" height="18" fill="var(--brand-red)"/><rect x="4" y="7" width="10" height="6" fill="none" stroke="#fff" stroke-width="1.4"/><rect x="6" y="3.5" width="6" height="3.5" fill="#fff"/></svg>
        505-627-1904
      </li>
      <li>
        <svg viewBox="0 0 18 18" aria-hidden="true"><rect width="18" height="18" fill="var(--brand-red)"/><rect x="3.5" y="5" width="11" height="8" fill="none" stroke="#fff" stroke-width="1.4"/><path d="M3.5 5 L9 10 L14.5 5" fill="none" stroke="#fff" stroke-width="1.4"/></svg>
        dorian@rvtfleetcars.example
      </li>
    </ul>

    <div class="person">
      <h2 class="person-name">Dorian Pellew</h2>
      <p class="person-title">Vice President</p>
      <div class="divider-right"></div>
      <address class="address">482 Morrow Ave NE<br>Mesa Ridge, NM 87190</address>
    </div>

    <div class="edge-band">
      <div class="edge-band-dark"></div>
      <div class="edge-band-red">www.RVTfleetcars.example</div>
    </div>
  </div>
</body>
</html>
```